Icon Design Project

Icon design for mobile site.

Site under development – viewable on pc or mobile at www.go.trellix.net/harborlane

Main site
www.harborlanesupport.co.uk
The branding is to be extended from the main site to the mobile site.

The site is nearly ready. I just need icons and buttons designed. If you visit www.go.trellix.net/harborlane you’ll see that I currently have text links instead of buttons. Looking at the site will help you understand where they go on the site.

Main menu icon set:
- ‘Special Offer’ button (not using Special Offer Image)
- ‘Services’ button
- ‘Contact’ button
- ‘Coffee?’ button
- ‘Video’ button

Category buttons.
These buttons need to integrate images with text. So that the buttons have image+text+border. All images provided with brief. Please go to www.harborlanesupport.co.uk to see how the main site uses them

These buttons should be large – covering nearly the entire width of the mobile page.

Buttons + Text as follows
Special Offer
Online Services
Local Marketing
Organisational Support
Tracking and Reporting
Websites
Mobile Sites
Training Portals
Local Search Optimisation
Call Tracking
SMS Campaigns
QR Campaigns
Mobile Ad Campaigns
Email Marketing
Social Media and Location Marketing
Tracking and Reporting

Please provide final buttons as transparent png/jpg.
Updates

Hi,

Thank you all for getting involved.

Some more detail on what I want.

The top menu: Special Offer - Services - Coffee - Contact, should be the width of the screen. Underneath should be a different looking video button.

Please make the top menu: Special Offer - Services - Coffee? - Contact buttons square with the text under an icon reflecting the buttons function. Graphically they need to stand out so don't feel you have to use the same grey as the menu on the main site (see brief for URL).

The video button can be longer and cover 1/3 to 1/2 the screen. This button should look different to the top menu buttons.

Hope this helps.

Marguerite

Dear all,

Looking forward to seeing your designs. Hope they come in quick so I can give you some feedback.

S

Target Market(s)

Businesses

Industry/Entity Type

Marketing

Requirements
Must have
• Must be in empathy with the design and colours found on site

```html
<!DOCTYPE html>
<html lang="en">
<head>
<meta charset="utf-8">
<title>Special Offer Button</title>
<link rel="stylesheet" href="https://fonts.googleapis.com/css2?family=Source+Sans+3:wght@400&display=swap">
<style>
  :root {
    --band-black: #000000;
    --heart-white: #ffffff;
    --page-white: #ffffff;
    --offer-red: #d40a0a;
  }
  html, body {
    margin: 0;
    padding: 0;
    overflow: hidden;
    background: var(--page-white);
  }
  .offer-button {
    position: relative;
    width: 1117px;
    height: 1200px;
    overflow: hidden;
    background: var(--page-white);
  }
  .offer-button__icon {
    position: absolute;
    left: 0;
    top: 0;
    display: block;
    width: 1117px;
    height: 976px;
  }
  .offer-button__band { fill: var(--band-black); }
  .offer-button__heart { fill: var(--heart-white); }
  .offer-button__label {
    position: absolute;
    left: 0;
    top: 976px;
    width: 1117px;
    margin: 0;
    text-align: center;
    font-family: "Source Sans 3", "Myriad Pro", sans-serif;
    font-weight: 400;
    font-size: 108px;
    line-height: 117px;
    color: var(--offer-red);
    padding-top: 4px;
  }
  .offer-button__label span { display: block; }
</style>
</head>
<body>
  <main class="offer-button">
    <svg class="offer-button__icon" viewBox="0 0 838 732" preserveAspectRatio="none" aria-hidden="true">
      <rect class="offer-button__band" x="0" y="0" width="838" height="732"/>
      <path class="offer-button__heart"
        d="M418,130
           C480,40 560,5 640,5
           C760,5 838,100 838,215
           C838,440 600,610 420,732
           C240,610 0,440 0,210
           C0,100 80,5 200,5
           C280,5 360,45 418,130 Z"/>
    </svg>
    <h1 class="offer-button__label">
      <span>Special</span>
      <span>Offer</span>
    </h1>
  </main>
</body>
</html>
```